Custom Wordpress Theme - Original and Professional

We are a boutique IT consulting firm that provide small and medium business in Australia three different levels of IT service.
We are looking for a developer who will create a customised, original and professional wordpress theme. We are looking for the developer to create a professional, clean, clear and simple theme with a stylish layout, images and icons.
Our three services are: IT support | IT Services | IT Solutions and we would like to clearly differentiate the difference in each level of service in as few words as possible.
IT Support is the ad hock “call us, when you need us” service, that smaller business or those with minimal issues use.
IT service is the unlimited service, that business with existing (and well maintained) IT systems choose and is both flexible and scalable including no contracts or paperwork required.
IT solutions are the unlimited service that businesses that need new or updated infrastructure choose and it includes all the hardware, software and services with no contracts or any ongoing commitment.
The main page on the web site will attract the visitor to choose the right “service level” for their business and then we will have a dedicated page for each service and another page for a comparison (table) to compare all three services.
Lastly we will need a contact us page that has both office locations (Sydney and Melbourne), contact phone numbers and an email form.
Items we are focused on for this project are: 1. Images, 2.Icons 3. Layout.
In summary we are looking for a custom WordPress theme into a 6 page (Home, IT Support, IT Services, IT Solutions, Compare Service levels and Contact us) website. The design must include relevant images and icons and be clear, simple, professional and sleek.

Thank you for your time and creativity and I look forward to working with you!

Target Market(s)

Small and Medium businesses in Australia

Industry/Entity Type

Boutique

Requirements
Must have
• - 6 Pages layout: Home, IT support, IT services, IT Solutions, Compare service levels and Contact us
- Images, Layout and Icons.
- Clean, Clear, Simple, Elegant, Stylish.
Nice to have
• - Some text (if possible but not required).
Should not have
• - Complexity.
- Confusing layout.
- Generic non matching images and icons.

```html
<!DOCTYPE html>
<html lang="en">
<head>
<meta charset="utf-8">
<title>Compare Service</title>
<link href="https://fonts.googleapis.com/css2?family=Droid+Serif&family=Ubuntu:wght@400;500&family=Arimo:wght@400;700&family=Marcellus&display=swap" rel="stylesheet">
<style>
:root{
  --ink:#1e1e1e;
  --muted:#8a8a8a;
  --accent:#39d6de;
  --footer:#3ddfe6;
  --coral:#f46d5b;
  --coral-dark:#e25544;
  --panel:#f7f7f7;
  --row:#ffffff;
  --rule:#ececec;
  --head-light:#7e7e7e;
  --head-dark:#4a4a4a;
  --grey-text:#8e8e8e;
  --orange:#e2644a;
  --yellow:#f2c12e;
}
*{margin:0;padding:0;box-sizing:border-box}
html,body{width:840px;height:1200px;overflow:hidden;background:#fff}
body{position:relative;font-family:"Ubuntu",sans-serif;color:var(--ink)}
.abs{position:absolute}
.brand{left:45px;top:56px;font-family:"Marcellus",serif;font-size:21px;letter-spacing:.3px}
.slogan{left:64px;top:84px;font-size:8px;color:var(--muted);text-transform:uppercase}
.nav{right:50px;top:64px;display:flex;gap:17px;font-size:12.5px}
.nav a{color:var(--ink);text-decoration:none}
.nav a.current{color:var(--accent)}
.hero{left:18px;top:121px;width:787px;height:268px;background:#fff;border:4px solid #b9b9b9;box-shadow:inset 0 0 18px 8px #cfcfcf;overflow:hidden}
.hero-line{position:absolute;width:560px;text-align:center;font-family:"Arimo",sans-serif;color:var(--grey-text);line-height:1}
.l1{left:36px;top:70px;font-size:52px}
.l2{left:36px;top:124px;font-size:60px;color:var(--yellow);font-weight:700}
.l3{left:36px;top:183px;font-size:55px}
.hot{color:var(--orange);font-weight:700}
.globe{left:550px;top:16px;width:200px;height:230px;border-radius:50%;background:radial-gradient(circle at 45% 60%,#e6edd6 0%,#a9be86 45%,#6e8e4f 75%,#fff 76%)}
.page-title{left:50px;top:412px;font-size:12.5px;color:#444}
.crumb{left:51px;top:431px;font-size:7px;color:var(--accent);font-style:italic;text-transform:uppercase}
.panel{left:30px;top:495px;width:690px;height:403px;background:var(--panel)}
.row{height:30px;border-bottom:1px solid var(--rule);background:linear-gradient(#fafafa,#f3f3f3)}
.head{color:#fff;font-family:"Arimo",sans-serif;text-align:center}
.head .name{font-size:13px;padding-top:8px;line-height:1.1}
.head .price{font-family:"Droid Serif",serif;font-size:26px;margin-top:6px;line-height:1}
.head .per{font-size:10.5px;color:#cfcfcf}
.basic{left:185px;top:509px;width:125px;height:80px;background:var(--head-light)}
.basic .band,.business .band{height:31px;background:#8c8c8c;border-bottom:1px solid #999}
.standard{left:311px;top:509px;width:120px;height:94px;background:var(--head-dark)}
.standard .band{height:45px;background:#555;border-bottom:1px solid #666}
.premium{left:430px;top:505px;width:131px;height:101px;background:var(--coral);border:1px solid var(--coral-dark)}
.premium .band{height:46px;border-bottom:1px solid #f79182}
.premium .name{font-weight:700;font-size:14px;padding-top:9px}
.premium .per{color:#fbb1a6}
.business{left:561px;top:509px;width:118px;height:80px;background:var(--head-dark)}
.business .band{background:#555}
.cell{font-size:12px;letter-spacing:.3px;white-space:nowrap}
.prod{left:72px}
.btn{height:22px;width:75px;font-family:"Arimo",sans-serif;font-size:11.5px;text-align:center;line-height:20px;border:1px solid #333;background:linear-gradient(#6a6a6a,#474747);color:#fff;color:#111}
.btn.coral{background:var(--coral);border-color:var(--coral-dark);border-radius:3px}
.footer{left:0;top:1153px;width:840px;height:47px;background:var(--footer);color:#fff;font-size:12px}
.footer .copy{position:absolute;left:54px;top:16px}
.social{position:absolute;right:40px;top:19px;display:flex;gap:4px}
.social span{width:7px;height:7px;border-radius:50%;background:#fff}
</style>
</head>
<body>
<div class="abs brand">COMPANY NAME</div>
<div class="abs slogan">Your company solgan</div>
<nav class="abs nav">
  <a href="#">Home</a><a href="#">IT support</a><a href="#">IT Services</a><a href="#">IT Solutions</a><a href="#" class="current">Compare Service</a><a href="#">Contact us</a>
</nav>

<section class="abs hero">
  <div class="hero-line l1">We <span class="hot">works</span> for</div>
  <div class="hero-line l2">making</div>
  <div class="hero-line l3">your <span class="hot">dreams</span> true</div>
  <div class="abs globe" role="img" aria-label="Green globe with a young plant sprouting from the top"></div>
</section>

<div class="abs page-title">Compare Service</div>
<div class="abs crumb">Home | Compare Service</div>

<section class="abs panel"></section>

<div class="abs head basic"><div class="band"><div class="name">BASIC PLAN</div></div><div class="price">$20</div><div class="per">per month</div></div>
<div class="abs head standard"><div class="band"><div class="name">STANDARD<br>PLAN</div></div><div class="price">$40</div><div class="per">per month</div></div>
<div class="abs head premium"><div class="band"><div class="name">PREMIUM<br>PLAN</div></div><div class="price">$60</div><div class="per">per month</div></div>
<div class="abs head business"><div class="band"><div class="name">BUSINESS PLAN</div></div><div class="price">$80</div><div class="per">per month</div></div>

<!-- product labels -->
<div class="abs cell prod" style="top:600px">PRODUCT 1</div>
<div class="abs cell prod" style="top:625px">PRODUCT 2</div>
<div class="abs cell prod" style="top:652px">PRODUCT 3</div>
<div class="abs cell prod" style="top:686px">PRODUCT 4</div>
<div class="abs cell prod" style="top:711px">PRODUCT 5</div>
<div class="abs cell prod" style="top:745px">PRODUCT 6</div>
<div class="abs cell prod" style="top:779px">PRODUCT 7</div>
<div class="abs cell prod" style="top:813px">PRODUCT 8</div>

<!-- basic -->
<div class="abs cell" style="left:207px;top:600px">Applicable</div>
<div class="abs cell" style="left:207px;top:625px">Applicable</div>
<div class="abs cell" style="left:207px;top:659px">Applicable</div>
<div class="abs cell" style="left:207px;top:688px">Applicable</div>
<div class="abs cell" style="left:207px;top:718px">Applicable</div>
<div class="abs cell" style="left:207px;top:750px">Applicable</div>
<div class="abs cell" style="left:207px;top:784px">Applicable</div>
<div class="abs cell" style="left:207px;top:809px">Applicable</div>

<!-- standard -->
<div class="abs cell" style="left:342px;top:609px">Applicable</div>
<div class="abs cell" style="left:342px;top:642px">Applicable</div>
<div class="abs cell" style="left:342px;top:674px">Applicable</div>
<div class="abs cell" style="left:342px;top:699px">Applicable</div>
<div class="abs cell" style="left:342px;top:733px">Applicable</div>
<div class="abs cell" style="left:342px;top:766px">Applicable</div>
<div class="abs cell" style="left:342px;top:800px">Applicable</div>
<div class="abs cell" style="left:342px;top:834px">Applicable</div>

<!-- premium -->
<div class="abs cell" style="left:467px;top:609px">Applicable</div>
<div class="abs cell" style="left:467px;top:642px">Applicable</div>
<div class="abs cell" style="left:467px;top:676px">Applicable</div>
<div class="abs cell" style="left:467px;top:706px">Applicable</div>
<div class="abs cell" style="left:467px;top:734px">Applicable</div>
<div class="abs cell" style="left:467px;top:766px">Applicable</div>
<div class="abs cell" style="left:467px;top:799px">Applicable</div>
<div class="abs cell" style="left:467px;top:833px">Applicable</div>

<!-- business -->
<div class="abs cell" style="left:583px;top:600px">Applicable</div>
<div class="abs cell" style="left:583px;top:626px">Applicable</div>
<div class="abs cell" style="left:583px;top:660px">Applicable</div>
<div class="abs cell" style="left:583px;top:688px">Applicable</div>
<div class="abs cell" style="left:583px;top:720px">Applicable</div>
<div class="abs cell" style="left:583px;top:750px">Applicable</div>
<div class="abs cell" style="left:583px;top:781px">Applicable</div>
<div class="abs cell" style="left:583px;top:815px">Applicable</div>

<div class="abs btn" style="left:210px;top:846px">Sign Up</div>
<div class="abs btn" style="left:336px;top:860px">Sign Up</div>
<div class="abs btn coral" style="left:458px;top:866px">Sign Up</div>
<div class="abs btn" style="left:578px;top:846px">Sign Up</div>

<footer class="abs footer">
  <div class="copy">IT SOLUTION© 2013 • Privacy Policy</div>
  <div class="social"><span></span><span></span><span></span><span></span></div>
</footer>
</body>
</html>
```